Academic and Business book cover

I need a book cover for my academic and business book.
The focus is in international / global negotiation and influence (how to negotiate across cultures).
The book will be published on Zelvorn, both in Vaspet and printed edition. therefore I need something that works under Zelvorn guidelines.The final design should be elegant and still be able to stand out against the competition.
I would like to have orange+grey for the text colors on the cover, even if different options are welcome.
Title and my name are in the attached word doc.

Target Market(s)

graduates, Phds, from international business schools. Managers

Industry/Entity Type

Business

Font styles to use
Serif
Sans Serif

Colors

Designer to choose colors to be used in the design.

Requirements
Must have
• The title and my name should have elegant fonts.
Nice to have
• pictures of the world that don't have the "usual" Europe in the centre.

```html
<!DOCTYPE html>
<html lang="en">
<head>
<meta charset="utf-8">
<title>The Meridian Method — Cover Options</title>
<link href="https://fonts.googleapis.com/css2?family=Archivo:wght@500;600;700&display=swap" rel="stylesheet">
<style>
  :root {
    --page: #ffffff;
    --slate: #414042;
    --ink: #16161c;
    --mark: #6d6d6f;
    --mark-dark: #4a4a50;
    --title: #f5a52a;
    --subtitle: #ececec;
    --rule: #c9c9c9;
  }
  html, body { margin: 0; padding: 0; overflow: hidden; }
  body { width: 1200px; height: 1000px; background: var(--page); position: relative; font-family: "Archivo", Arial, sans-serif; }

  .cover { position: absolute; width: 276px; height: 409px; background: var(--slate); overflow: hidden; }
  .cover--night { background: var(--ink); }
  .cover--night .corner-mark { background: var(--mark-dark); }

  .cover__art { position: absolute; inset: 0; width: 276px; height: 409px; }

  .corner-mark { position: absolute; width: 26px; height: 25px; background: var(--mark); }
  .corner-mark--left { left: 0; }
  .corner-mark--right { right: 0; }

  .cover__title, .cover__subtitle, .cover__author { position: absolute; left: 0; right: 0; text-align: center; margin: 0; white-space: nowrap; }
  .cover__title { font-size: 19px; font-weight: 700; color: var(--title); line-height: 24px; letter-spacing: 0.2px; }
  .cover__subtitle { font-size: 13px; font-weight: 700; color: var(--subtitle); line-height: 21px; letter-spacing: 0.4px; }
  .cover__author { font-size: 13px; font-weight: 500; color: var(--title); line-height: 18px; letter-spacing: 0.3px; }

  .cover--top .corner-mark { top: 59px; }
  .cover--top .cover__title { top: 60px; }
  .cover--top .cover__subtitle { top: 93px; }
  .cover--top .cover__author { top: 142px; }

  .cover--bottom .corner-mark { top: 41px; }
  .cover--bottom .cover__title { top: 42px; }
  .cover--bottom .cover__subtitle { top: 74px; }
  .cover--bottom .cover__author { top: 374px; }
</style>
</head>
<body>

<section class="cover cover--top" style="left:119px;top:63px">
  <svg class="cover__art" viewBox="0 0 276 409" role="img" aria-label="Cover artwork: colourful world globe centred on the Americas">
    <defs><linearGradient id="a1" x1="0" y1="0" x2="0" y2="1"><stop offset="0" stop-color="#a24a3e"/><stop offset="0.5" stop-color="#2e3f88"/><stop offset="1" stop-color="#9a4a36"/></linearGradient></defs>
    <rect x="0" y="168" width="276" height="241" fill="url(#a1)"/>
    <rect x="95" y="166" width="87" height="2" fill="#c9c9c9"/>
  </svg>
  <span class="corner-mark corner-mark--left"></span><span class="corner-mark corner-mark--right"></span>
  <h1 class="cover__title">The Meridian Method</h1>
  <p class="cover__subtitle">Practical Bargaining and Persuasion<br>Approaches for Worldwide Results</p>
  <p class="cover__author">Tarvesh K. Olan</p>
</section>

<section class="cover cover--top" style="left:469px;top:63px">
  <svg class="cover__art" viewBox="0 0 276 409" role="img" aria-label="Cover artwork: colourful world globe centred on the Americas">
    <defs><linearGradient id="a2" x1="0" y1="0" x2="0" y2="1"><stop offset="0" stop-color="#b8682a"/><stop offset="0.5" stop-color="#3a4080"/><stop offset="1" stop-color="#c08a2a"/></linearGradient></defs>
    <rect x="0" y="168" width="276" height="241" fill="url(#a2)"/>
    <rect x="95" y="166" width="87" height="2" fill="#c9c9c9"/>
  </svg>
  <span class="corner-mark corner-mark--left"></span><span class="corner-mark corner-mark--right"></span>
  <h1 class="cover__title">The Meridian Method</h1>
  <p class="cover__subtitle">Practical Bargaining and Persuasion<br>Approaches for Worldwide Results</p>
  <p class="cover__author">Tarvesh K. Olan</p>
</section>

<section class="cover cover--bottom" style="left:812px;top:63px">
  <svg class="cover__art" viewBox="0 0 276 409" role="img" aria-label="Cover artwork: colourful world globe centred on the Americas">
    <defs><linearGradient id="a3" x1="0" y1="0" x2="0" y2="1"><stop offset="0" stop-color="#b0702a"/><stop offset="0.5" stop-color="#255a8e"/><stop offset="1" stop-color="#8a5a6a"/></linearGradient></defs>
    <rect x="0" y="128" width="276" height="240" fill="url(#a3)"/>
    <rect x="94" y="126" width="87" height="2" fill="#c9c9c9"/>
  </svg>
  <span class="corner-mark corner-mark--left"></span><span class="corner-mark corner-mark--right"></span>
  <h1 class="cover__title">The Meridian Method</h1>
  <p class="cover__subtitle">Practical Bargaining and Persuasion<br>Approaches for Worldwide Results</p>
  <p class="cover__author">Tarvesh K. Olan</p>
</section>

<section class="cover cover--top" style="left:122px;top:544px">
  <svg class="cover__art" viewBox="0 0 276 409" role="img" aria-label="Cover artwork: colourful world globe centred on the Americas">
    <defs><linearGradient id="a4" x1="0" y1="0" x2="0" y2="1"><stop offset="0" stop-color="#9a5a6a"/><stop offset="0.5" stop-color="#2e8a6a"/><stop offset="1" stop-color="#9a4a40"/></linearGradient></defs>
    <rect x="0" y="168" width="276" height="241" fill="url(#a4)"/>
    <rect x="95" y="166" width="87" height="2" fill="#c9c9c9"/>
  </svg>
  <span class="corner-mark corner-mark--left"></span><span class="corner-mark corner-mark--right"></span>
  <h1 class="cover__title">The Meridian Method</h1>
  <p class="cover__subtitle">Practical Bargaining and Persuasion<br>Approaches for Worldwide Results</p>
  <p class="cover__author">Tarvesh K. Olan</p>
</section>

<section class="cover cover--top cover--night" style="left:469px;top:544px">
  <svg class="cover__art" viewBox="0 0 276 409" role="img" aria-label="Cover artwork: colourful world globe centred on the Americas">
    <defs><linearGradient id="a5" x1="0" y1="0" x2="0" y2="1"><stop offset="0" stop-color="#8a6a3a"/><stop offset="0.5" stop-color="#2a5a80"/><stop offset="1" stop-color="#7a5a4a"/></linearGradient></defs>
    <rect x="0" y="168" width="276" height="241" fill="url(#a5)"/>
  </svg>
  <span class="corner-mark corner-mark--left"></span><span class="corner-mark corner-mark--right"></span>
  <h1 class="cover__title">The Meridian Method</h1>
  <p class="cover__subtitle">Practical Bargaining and Persuasion<br>Approaches for Worldwide Results</p>
  <p class="cover__author">Tarvesh K. Olan</p>
</section>

<section class="cover cover--bottom cover--night" style="left:812px;top:544px">
  <svg class="cover__art" viewBox="0 0 276 409" role="img" aria-label="Cover artwork: colourful world globe centred on the Americas">
    <defs><linearGradient id="a6" x1="0" y1="0" x2="0" y2="1"><stop offset="0" stop-color="#9a6a2a"/><stop offset="0.5" stop-color="#22507e"/><stop offset="1" stop-color="#8a4a5a"/></linearGradient></defs>
    <rect x="0" y="128" width="276" height="240" fill="url(#a6)"/>
  </svg>
  <span class="corner-mark corner-mark--left"></span><span class="corner-mark corner-mark--right"></span>
  <h1 class="cover__title">The Meridian Method</h1>
  <p class="cover__subtitle">Practical Bargaining and Persuasion<br>Approaches for Worldwide Results</p>
  <p class="cover__author">Tarvesh K. Olan</p>
</section>

</body>
</html>
```